Coastal Learner Bureau business cards

Australian company about to start offering its services. We recruit international students to come to study English, vocational education and postgraduate courses in Australia. We help them find the institution and select the right city they want to come to Australia. We are a young, online oriented and supportive agency. Our clients are between 18 and 35 years old, mainly University students, young professionals or people with work experience. We provide much more information that any other agency offer. We administrate a Facebook group with more than 11.000 members that daily ask questions about general information when coming to Australia, while they are here and even after they leave the country

Target Market(s)

International students from South America, Central America and Europe

Industry/Entity Type

Student

Contact Information for Business Card

Tomas Bilbrea
Managing Director
tomas@kelvarin.com.au
www.kelvoria.com.au
+61 491058264
Melbourne, Australia

Font styles to use
Serif
Sans Serif

Colors

Designer to choose colors to be used in the design.

Requirements
Must have
• Horizontal design
• Standard business card size and shape. If font uses green or yellow colours, they will have to match the ones from the logo
Nice to have
• UPDATE: Use the contents of the green image to design one of the card sides. Use our logo in the background of that side as watermark.
• Passport image, or immigration stamps. A picture of the Yarra River (from Melbourne) would be cool as well.
Should not have
• Non-standard business card size and shape
• Not black as the background colour of any sides as we are not a VIP agency or a hight class service. We are orientes to young people and they like colours, pictures, something attractive.
• Vertical design
• NO YELLOW or BLACK AS THE BACKGROUND COLOUR OF ANY SIDE OF THE BIZ CARD

```html
<!DOCTYPE html>
<html lang="en">
<head>
<meta charset="utf-8">
<title>Coastal Learner Bureau business cards</title>
<link href="https://fonts.googleapis.com/css2?family=Noto+Sans:wght@400;600;700&display=swap" rel="stylesheet">
<style>
  :root {
    --bg: #111111;
    --yellow: #ecc619;
    --green: #0f6b45;
    --paper: #fbfaf6;
    --ink: #2b2b2b;
  }
  * { box-sizing: border-box; margin: 0; padding: 0; }
  html, body { width: 1200px; height: 1000px; overflow: hidden; background: var(--bg); }
  body { position: relative; font-family: "Noto Sans", sans-serif; }

  .card {
    position: absolute;
    width: 520px;
    height: 300px;
    border-radius: 18px;
    overflow: hidden;
  }

  /* Front side */
  .card-front {
    left: 60px; top: 200px;
    background: var(--green);
    display: flex; align-items: center; justify-content: center;
  }
  .brand {
    display: flex; align-items: center; gap: 12px;
    color: var(--green);
    font-weight: 700;
  }
  .brand-dot { border-radius: 50%; background: var(--green); flex: none; }
  .card-front .brand { font-size: 50px; color: var(--yellow); }
  .card-front .brand-dot { width: 26px; height: 26px; background: var(--yellow); }

  /* Back side */
  .card-back {
    left: 620px; top: 480px;
    background: var(--paper);
  }
  .card-back .brand {
    position: absolute; left: 34px; top: 78px;
    font-size: 34px;
  }
  .card-back .brand-dot { width: 18px; height: 18px; }

  .identity { position: absolute; left: 300px; top: 58px; }
  .person-name { font-size: 20px; font-weight: 700; color: var(--green); line-height: 1.1; }
  .person-name .surname { color: var(--yellow); }
  .person-role { font-size: 13px; color: var(--ink); margin-top: 2px; }

  .contact-list { list-style: none; margin-top: 18px; }
  .contact-list li {
    display: flex; align-items: center; gap: 8px;
    font-size: 14px; color: var(--ink); line-height: 22px;
  }
  .contact-list svg { width: 13px; height: 13px; fill: var(--green); flex: none; }

  .base-band { position: absolute; left: 0; bottom: 0; width: 520px; height: 90px; }
  .city {
    position: absolute; left: 20px; bottom: 20px; width: 290px;
    text-align: center; color: #ffffff; font-size: 15px;
  }
</style>
</head>
<body>

<section class="card card-front" aria-label="Business card front">
  <div class="brand"><span class="brand-dot"></span><span>Kelvoria</span></div>
</section>

<section class="card card-back" aria-label="Business card back">
  <div class="brand"><span class="brand-dot"></span><span>Kelvoria</span></div>

  <div class="identity">
    <p class="person-name">Tomas <span class="surname">Bilbrea</span></p>
    <p class="person-role">Managing Director</p>
    <ul class="contact-list">
      <li>
        <svg viewBox="0 0 16 16" aria-hidden="true"><path d="M3.6 1.2l2.3 2.9-1.2 1.7c.9 2 2.5 3.6 4.5 4.5l1.7-1.2 2.9 2.3-1.4 2.5C7 13.6 2.4 9 1.1 2.6z"/></svg>
        +61 491058264
      </li>
      <li>
        <svg viewBox="0 0 16 16" aria-hidden="true"><path d="M1 3h14v1.2L8 9 1 4.2z M1 5.8l7 4.8 7-4.8V13H1z"/></svg>
        tomas@kelvarin.com.au
      </li>
      <li>
        <svg viewBox="0 0 16 16" aria-hidden="true"><path d="M8 1a7 7 0 100 14A7 7 0 008 1zm4.9 6h-2.4a10 10 0 00-1-4.3A5.5 5.5 0 0112.9 7zM8 2.6c.7 1 1.2 2.6 1.3 4.4H6.7C6.8 5.2 7.3 3.6 8 2.6zM6.5 2.7A10 10 0 005.5 7H3.1a5.5 5.5 0 013.4-4.3zM3.1 9h2.4a10 10 0 001 4.3A5.5 5.5 0 013.1 9zM8 13.4c-.7-1-1.2-2.6-1.3-4.4h2.6c-.1 1.8-.6 3.4-1.3 4.4zm1.5-.1a10 10 0 001-4.3h2.4a5.5 5.5 0 01-3.4 4.3z"/></svg>
        www.kelvoria.com.au
      </li>
    </ul>
  </div>

  <svg class="base-band" viewBox="0 0 520 90" aria-hidden="true">
    <path fill="#0f6b45" d="M0 40 H22 Q22 22 40 22 H300 Q318 22 318 40 V46 Q318 58 330 58 H520 V90 H0 Z"/>
  </svg>
  <p class="city">Melbourne, Australia</p>
</section>

</body>
</html>
```